Harborline Auto LLC

Car Dealer Customer Service
Address: 2874 Cresthaven Road, Shelbyville, TN 37162
web: www.harborlineautoxq.net
email: harborlineautoxq@mailnest.example
Phone: (931) 555-0148
Phone: (629) 555-0173

```html
<!DOCTYPE html>
<html lang="en">
<head>
<meta charset="utf-8">
<title>Harborline Auto LLC – Business Card</title>
<link href="https://fonts.googleapis.com/css2?family=Lexend:wght@600;700&family=Poppins:ital,wght@0,400;0,600;1,400&display=swap" rel="stylesheet">
<style>
  :root{
    --bg:#2a2a2a;
    --card:#f1f1f1;
    --blue:#1b73a3;
    --gold:#e2a63c;
    --ink:#1e1e1e;
    --white:#ffffff;
    --faint:#dde8ef;
  }
  *{margin:0;padding:0;box-sizing:border-box}
  html,body{width:1200px;height:1138px;overflow:hidden;background:var(--bg)}
  body{position:relative;font-family:"Poppins",sans-serif;color:var(--ink)}
  .card{position:absolute;width:620px;height:375px;background:var(--card);border-radius:14px;overflow:hidden}
  .card--front{left:274px;top:186px}
  .card--back{left:276px;top:608px}

  /* front */
  .front__halo{position:absolute;left:320px;top:-30px;width:300px;height:300px;border-radius:50%;background:var(--faint);opacity:.6}
  .front__mark{position:absolute;left:271px;top:84px;width:80px;height:80px;border-radius:50%;background:var(--blue)}
  .front__name{position:absolute;left:0;right:0;top:210px;text-align:center;font-family:"Lexend",sans-serif;font-weight:700;font-size:31px;letter-spacing:.5px;color:var(--blue)}
  .front__web{position:absolute;left:0;right:0;top:322px;display:flex;justify-content:center;align-items:center;gap:24px;font-size:15px}
  .front__rule{width:54px;height:2px;background:var(--gold)}
  .front__bands{position:absolute;left:0;right:0;bottom:0;height:18px;display:flex}
  .front__bands span{flex:1}
  .band-blue{background:var(--blue)}
  .band-gold{background:var(--gold)}

  /* back */
  .back__title{position:absolute;left:28px;top:40px;font-family:"Lexend",sans-serif;font-weight:700;font-size:42px;letter-spacing:.5px;color:var(--blue)}
  .back__blue{position:absolute;left:0;right:0;top:118px;height:138px;background:var(--blue)}
  .back__gold{position:absolute;left:0;right:0;top:256px;height:64px;background:var(--gold)}
  .back__role{position:absolute;left:28px;top:140px;font-style:italic;font-size:17px;color:var(--white)}
  .back__phones{position:absolute;left:28px;top:174px;list-style:none}
  .back__phones li{display:flex;align-items:center;gap:12px;height:29px;font-weight:600;font-size:22px;letter-spacing:.5px;color:var(--white)}
  .back__links{position:absolute;left:28px;top:264px;list-style:none}
  .back__links li{display:flex;align-items:center;gap:12px;height:22px;font-size:15px}
  .back__address{position:absolute;left:28px;top:326px;font-size:16px}
  .back__mark{position:absolute;left:344px;top:112px;width:220px;height:220px;border-radius:50%;background:var(--white);display:flex;align-items:center;justify-content:center;text-align:center;font-family:"Lexend",sans-serif;font-weight:700;font-size:24px;line-height:1.2;color:var(--blue)}
  svg{flex:none}
</style>
</head>
<body>

<section class="card card--front">
  <div class="front__halo"></div>
  <div class="front__mark"></div>
  <div class="front__name">HARBORLINE AUTO</div>
  <div class="front__web"><span class="front__rule"></span><span>www.harborlineautoxq.net</span><span class="front__rule"></span></div>
  <div class="front__bands"><span class="band-blue"></span><span class="band-gold"></span></div>
</section>

<section class="card card--back">
  <h1 class="back__title">HARBORLINE AUTO</h1>
  <div class="back__blue"></div>
  <div class="back__gold"></div>
  <p class="back__role">Car Dealer Customer Service</p>
  <ul class="back__phones">
    <li><svg width="20" height="18" viewBox="0 0 20 18"><path d="M2 6c0-3 4-4 8-4s8 1 8 4v2h-4V6H6v2H2z" fill="#e2a63c"/><rect x="4" y="9" width="12" height="8" rx="2" fill="#e2a63c"/></svg>931-555-0148</li>
    <li><svg width="20" height="18" viewBox="0 0 20 18"><path d="M2 6c0-3 4-4 8-4s8 1 8 4v2h-4V6H6v2H2z" fill="#e2a63c"/><rect x="4" y="9" width="12" height="8" rx="2" fill="#e2a63c"/></svg>629-555-0173</li>
  </ul>
  <ul class="back__links">
    <li><svg width="14" height="14" viewBox="0 0 14 14" fill="none" stroke="#1e1e1e" stroke-width="1.4"><circle cx="7" cy="7" r="6"/><path d="M1 7h12M7 1c3 3 3 9 0 12M7 1c-3 3-3 9 0 12"/></svg>www.harborlineautoxq.net</li>
    <li><svg width="14" height="12" viewBox="0 0 14 12"><rect x="0.5" y="1" width="13" height="10" fill="#1e1e1e"/><path d="M1 1.5l6 5 6-5" fill="none" stroke="#e2a63c" stroke-width="1.4"/></svg>harborlineautoxq@mailnest.example</li>
  </ul>
  <p class="back__address">2874 Cresthaven Road, Shelbyville, TN 37162</p>
  <div class="back__mark">HARBORLINE<br>AUTO</div>
</section>

</body>
</html>
```